Brovanek Data Yellow rose letterhead

I have a new logo for my company but in its current form it is too large to be used on letterhead or as a email signature. I need to have the designer use elements from the current logo and create something close to the original but more suited for smaller items.
Updates

I just uploaded a copy of our logo that does not have the weathered affect. Thanks

Reason: More time for revisions

Industry/Entity Type

It Company

Requirements
Must have
• The design must maintain the visual effect of the current logo. It needs to include the yellow rose and the name of the company.
Nice to have
• It would be nice to maintain the stamp theme and incorporate my name, address, phone, email. etc.

```html
<!DOCTYPE html>
<html lang="en">
<head>
<meta charset="utf-8">
<title>Brovanek Data Letterhead</title>
<link rel="stylesheet" href="https://fonts.googleapis.com/css2?family=Questrial&display=swap">
<style>
  :root {
    --backdrop: #e8e5e0;
    --paper: #ffffff;
    --ink: #1f1f1f;
    --brand-brown: #4a3f3a;
    --brand-teal: #2bb3b8;
    --brand-orange: #f0913a;
  }
  * { margin: 0; padding: 0; box-sizing: border-box; }
  html, body {
    width: 1054px;
    height: 1200px;
    overflow: hidden;
    background: var(--backdrop);
  }
  .letterhead {
    position: absolute;
    left: 137px;
    top: 48px;
    width: 780px;
    height: 1103px;
    background: var(--paper);
    box-shadow: 0 2px 10px rgba(0,0,0,0.18);
    font-family: "Questrial", "Century Gothic", sans-serif;
  }
  .header-swoosh {
    position: absolute;
    left: 0;
    top: 120px;
    width: 780px;
    height: 100px;
  }
  .brand {
    position: absolute;
    left: 41px;
    top: 74px;
    display: flex;
    align-items: center;
    gap: 16px;
  }
  .brand-mark {
    width: 54px;
    height: 54px;
    background: var(--brand-orange);
  }
  .brand-name {
    font-size: 34px;
    font-weight: 400;
    color: var(--brand-brown);
    letter-spacing: 0.5px;
  }
  .sender {
    position: absolute;
    left: 456px;
    top: 24px;
    color: var(--ink);
    font-size: 19px;
    line-height: 25px;
    font-style: normal;
  }
  .sender-name { font-size: 17px; }
</style>
</head>
<body>
  <main class="letterhead">
    <svg class="header-swoosh" viewBox="0 0 780 100" aria-hidden="true">
      <path d="M0 62 Q 380 28 780 36 L780 48 Q 380 42 0 76 Z" fill="var(--brand-brown)"/>
      <path d="M0 76 Q 380 42 780 48 L780 58 Q 380 52 0 86 Z" fill="var(--brand-teal)"/>
    </svg>

    <div class="brand">
      <div class="brand-mark"></div>
      <span class="brand-name">Brovanek Data</span>
    </div>

    <address class="sender">
      <div class="sender-name">Maren Colwell, PhD</div>
      <div>218 NW Cedar Ridge Way, Ste 1140</div>
      <div>Marlow Falls, TX 76512</div>
      <div>1-800-555-0148</div>
      <div>maren@brovanek-data.com</div>
    </address>
  </main>
</body>
</html>
```